Tech business card design

We need an amazing business card design for our new business 'Pexla' a marketing tech startup based in Sydney, Australia. We provide an online marketplace for businesses to search and buy advertising media, connect with service providers and learn more about marketing. We wish to communicate 'cool tech', reliability and professionalism and design based around our logo.

Target Market(s)

Business Owners

Contact Information for Business Card

Name
Position
Email Address
Website
Phone Number

Font styles to use
Other font styles liked:
• Avenir & Avenir Next

Colors

Designer to choose colors to be used in the design.

```html
<!DOCTYPE html>
<html lang="en">
<head>
<meta charset="utf-8">
<title>Pexla Business Card</title>
<link rel="stylesheet" href="https://fonts.googleapis.com/css2?family=Lato:wght@300;400;900&display=swap">
<style>
  :root {
    --stage: #e4e5e8;
    --navy-deep: #14144a;
    --navy: #1d1f55;
    --navy-light: #272a63;
    --paper: #fbf7f8;
    --ink-white: #ffffff;
    --ink-soft: #c9cbe0;
  }
  * { margin: 0; padding: 0; box-sizing: border-box; }
  html, body {
    width: 1200px; height: 782px; overflow: hidden;
    background: var(--stage);
    font-family: "Lato", sans-serif;
  }
  .stage {
    position: relative; width: 1200px; height: 782px;
  }
  .card {
    position: absolute; top: 236px;
    width: 520px; height: 310px;
    overflow: hidden;
    box-shadow: 0 6px 18px rgba(0,0,0,0.18);
  }
  /* Front */
  .card-front { left: 50px; background: linear-gradient(180deg, var(--navy-light), var(--navy-deep)); }
  .front-edge {
    position: absolute; left: 0; top: 0; width: 58px; height: 100%;
    background: var(--navy-deep);
  }
  .front-band {
    position: absolute; left: 58px; top: 0; width: 138px; height: 100%;
    background: var(--paper);
  }
  .front-brand {
    position: absolute; left: 127px; top: 155px;
    transform: translate(-50%, -50%) rotate(-90deg);
    font-weight: 900; font-size: 84px; letter-spacing: -2px;
    color: var(--navy); line-height: 1; white-space: nowrap;
  }
  .front-details {
    position: absolute; left: 232px; top: 96px; color: var(--ink-white);
  }
  .person-name {
    font-weight: 900; font-size: 22px; letter-spacing: 1px; text-transform: uppercase;
  }
  .person-role {
    font-weight: 300; font-size: 15px; color: var(--ink-soft); margin-top: 2px;
  }
  .contact-list { list-style: none; margin-top: 22px; }
  .contact-item {
    display: flex; align-items: center; gap: 9px;
    font-weight: 400; font-size: 16px; line-height: 25px; color: var(--ink-white);
  }
  .contact-icon { width: 13px; height: 13px; fill: var(--ink-white); flex: none; }
  /* Back */
  .card-back { left: 630px; background: var(--navy-deep); }
  .back-texture {
    position: absolute; inset: 0;
    background: linear-gradient(135deg, var(--navy-deep), #1a1b52 60%, var(--navy-deep));
  }
  .back-brand {
    position: absolute; right: 74px; bottom: 72px;
    font-weight: 900; font-size: 34px; letter-spacing: -0.5px;
    color: var(--ink-white); line-height: 1;
  }
</style>
</head>
<body>
<main class="stage">
  <section class="card card-front" aria-label="Business card front">
    <div class="front-edge"></div>
    <div class="front-band"></div>
    <div class="front-brand">Pexla</div>
    <div class="front-details">
      <h1 class="person-name">Marcus Hale</h1>
      <p class="person-role">Managing Director</p>
      <ul class="contact-list">
        <li class="contact-item">
          <svg class="contact-icon" viewBox="0 0 16 16" aria-hidden="true"><path d="M3.5 1.5l2.5 0 1.2 3.3-1.7 1.2c.9 1.9 2.4 3.4 4.3 4.3l1.2-1.7 3.3 1.2v2.5c0 .9-.7 1.5-1.5 1.5C6.8 13.8 2.2 9.2 2 3c0-.8.6-1.5 1.5-1.5z"/></svg>
          044-987 654 321
        </li>
        <li class="contact-item">
          <svg class="contact-icon" viewBox="0 0 16 16" aria-hidden="true"><path d="M1 3h14v10H1z M2.5 4.5L8 8.8l5.5-4.3" fill="none" stroke="#fff" stroke-width="1.6"/></svg>
          hello@pexla.com
        </li>
        <li class="contact-item">
          <svg class="contact-icon" viewBox="0 0 16 16" aria-hidden="true"><circle cx="8" cy="8" r="6.5" fill="none" stroke="#fff" stroke-width="1.5"/><path d="M1.5 8h13M8 1.5c-2.4 3.6-2.4 9.4 0 13M8 1.5c2.4 3.6 2.4 9.4 0 13" fill="none" stroke="#fff" stroke-width="1.2"/></svg>
          www.pexla.com
        </li>
      </ul>
    </div>
  </section>

  <section class="card card-back" aria-label="Business card back">
    <div class="back-texture" role="img" aria-label="Subtle repeating brand-name pattern in dark navy tones"></div>
    <div class="back-brand">Pexla</div>
  </section>
</main>
</body>
</html>
```